Business Card for Multi-Brand Sportswear Company

We are looking for a business card which represents our company and the multiple brands within it.

The company: Fen Athletics (LTD)
The brands: Fen, TavaPuni, ElmStretch, Grit and Rain

Employees using these cards would be representing Fen Athletics, rather than any of the individual brands. You will see a current design within the uploaded files, to give some inspiration. The actual text of the brands is not necessary, but the logos should be on there is some format.

Our creative minds on this are stretched, so we are looking for someone to make this their own, and show us what a good business card should look like.

We may like to get these printed with spot gloss, so keep that in mind with your designs.

www.fenathletics.co.uk

Industry/Entity Type

Business

Contact Information for Business Card

Leo Pemberton-Hale
Operations Manager
(+44) 1632 960 418
Leo@fenathletics.co.uk
www.fenathletics.co.uk

Font styles to use
Sans Serif
Other font styles liked:
• Eurostile

Colors
ffffff

Requirements
Nice to have
• Dark (black) background

```html
<!DOCTYPE html>
<html lang="en">
<head>
<meta charset="utf-8">
<title>Fen Athletics – Business Card</title>
<link rel="stylesheet" href="https://fonts.googleapis.com/css2?family=Roboto:wght@500;700&family=Saira:wght@400;500;600&display=swap">
<style>
  :root {
    --backdrop: #3b3b3b;
    --brand-red: #ec1c24;
    --ink: #111111;
    --paper: #ffffff;
    --text-grey: #555555;
  }
  * { box-sizing: border-box; margin: 0; padding: 0; }
  html, body {
    width: 1105px; height: 1200px; overflow: hidden;
    background: var(--backdrop);
  }
  .sheet { position: relative; width: 1105px; height: 1200px; }
  .card {
    position: absolute; left: 196px; width: 720px; height: 412px;
    overflow: hidden;
    box-shadow: 0 4px 10px rgba(0,0,0,.45);
  }
  .card--front { top: 146px; background: var(--paper); }
  .card--back { top: 602px; background: var(--brand-red); }
  .front-art { position: absolute; inset: 0; }

  .holder { position: absolute; right: 40px; top: 28px; text-align: right; color: var(--paper); }
  .holder__name { font: 700 25px/1.1 "Roboto", sans-serif; }
  .holder__title { font: 400 18px/1.4 "Saira", sans-serif; margin-top: 2px; }

  .wordmark {
    position: absolute; font: 600 40px/1 "Saira", sans-serif;
    letter-spacing: 1px; display: flex; align-items: center; gap: 12px;
  }
  .wordmark__dot { width: 20px; height: 20px; border-radius: 50%; background: var(--brand-red); }
  .wordmark--front { left: 40px; top: 190px; color: var(--ink); }
  .wordmark--back { left: 0; right: 0; top: 172px; justify-content: center; color: var(--paper); font-size: 52px; }
  .wordmark--back .wordmark__dot { background: var(--paper); width: 24px; height: 24px; }

  .contact { position: absolute; left: 40px; top: 296px; list-style: none; }
  .contact li {
    display: flex; align-items: center; gap: 10px; height: 28px;
    font: 400 18px/1 "Saira", sans-serif; color: var(--text-grey);
  }
  .contact svg { width: 17px; height: 17px; fill: var(--brand-red); flex: none; }

  .address {
    position: absolute; right: 40px; top: 324px; text-align: right;
    font: 400 18px/28px "Saira", sans-serif; color: var(--text-grey); font-style: normal;
  }

  .brands {
    position: absolute; left: 0; right: 0; top: 330px; list-style: none;
    display: flex; justify-content: center; gap: 26px;
    font: 600 17px/1 "Saira", sans-serif; color: var(--paper);
  }
</style>
</head>
<body>
<main class="sheet">
  <section class="card card--front" aria-label="Business card front">
    <svg class="front-art" viewBox="0 0 720 412" aria-hidden="true">
      <path d="M0 0 H720 V236 C560 120 330 50 0 72 Z" fill="var(--brand-red)"/>
      <path d="M0 72 C330 50 560 120 720 236 V254 C560 136 330 58 0 76 Z" fill="var(--ink)"/>
    </svg>
    <div class="holder">
      <p class="holder__name">Leo Pemberton-Hale</p>
      <p class="holder__title">Operations Manager</p>
    </div>
    <div class="wordmark wordmark--front"><span class="wordmark__dot"></span>Fen Athletics</div>
    <ul class="contact">
      <li><svg viewBox="0 0 24 24"><path d="M6.6 10.8a15 15 0 0 0 6.6 6.6l2.2-2.2a1 1 0 0 1 1-.25 11.4 11.4 0 0 0 3.6.57 1 1 0 0 1 1 1V20a1 1 0 0 1-1 1A17 17 0 0 1 3 4a1 1 0 0 1 1-1h3.5a1 1 0 0 1 1 1c0 1.25.2 2.45.57 3.57a1 1 0 0 1-.25 1z"/></svg>(+44) 1632 960 418</li>
      <li><svg viewBox="0 0 24 24"><path d="M2 5h20v14H2z M2 5l10 8 10-8" stroke="#fff" stroke-width="1.5"/></svg>Leo@fenathletics.co.uk</li>
      <li><svg viewBox="0 0 24 24"><circle cx="12" cy="12" r="10"/></svg>www.fenathletics.co.uk</li>
    </ul>
    <address class="address">Marsh Row, Elmbury<br>Fenton, FN4 2QD</address>
  </section>

  <section class="card card--back" aria-label="Business card back">
    <div class="wordmark wordmark--back"><span class="wordmark__dot"></span>Fen Athletics</div>
    <ul class="brands">
      <li>TavaPuni</li>
      <li>ElmStretch</li>
      <li>Grit and Rain</li>
      <li>Fen</li>
    </ul>
  </section>
</main>
</body>
</html>
```